Cat-products company needs smart, yet endearing, business card

We need a business card design for a new, but up-and-running, business based in Honolulu, Hawaii. The business is Purrnest Nook Co. Our first product is the most environmentally-friendly cat grass kit ever seen on the planet. Future products, currently in the R&D phase, will include a variety of exciting cat scratchers. We also do consulting work to help apartment-dwellers make their home more cat-friendly and, in the future, plan on doing full, custom installs of structure to create high walkways for cats.

Target Market(s)

Middle-aged, apartment-dwelling, middle-class workers who own 1 or more cats and who dote on them.

Industry/Entity Type

Pet Care

Contact Information for Business Card

A striking, professional, yet warm and friendly design is what we're after.

Font styles to use
Serif
Sans Serif
Other font styles liked:
• Comfortaa

Colors

Designer to choose colors to be used in the design.

Requirements
Must have
• The company logo: (see attachment)
• The company name: Purrnest Nook Co
• The web address: www.purrnestnookco.com
• Email: support@purrnestnookco.com
• Phone: +1 (808) 571 6023
• Update (Fri Jun 30 3017 7:45pm Hawaii Time) I would like, is possible, uploaded picture of the cat grass kit on the back of the card with some text along the lines of: Purrnest Nook Co - Maker Of The Leafiest Feline Sprout Set Yet
Nice to have
• A cat picture, cartoon, real or silhouette that illustrates cats in action and/or relaxing; ie using the apartment space to live, play and relax in and being well-contented.
• Most of the website is done in the font: Comfortaa. It might be nice to continue using this for brand consistency.
Should not have
• Hard-to-read fonts.

```html
<!DOCTYPE html>
<html lang="en">
<head>
<meta charset="utf-8">
<title>Purrnest Nook Co – Business Card</title>
<link href="https://fonts.googleapis.com/css2?family=Montserrat:wght@600;700&family=Questrial&display=swap" rel="stylesheet">
<style>
  :root {
    --brown: #4e2c24;
    --yellow: #f4ac1c;
    --white: #ffffff;
    --page: #ececec;
    --text-dark: #3b2520;
    --line: #6b4a40;
  }
  html, body {
    margin: 0;
    padding: 0;
    width: 1200px;
    height: 880px;
    overflow: hidden;
    background: var(--page);
  }
  .canvas {
    position: relative;
    width: 1200px;
    height: 880px;
  }
  .card {
    position: absolute;
    left: 260px;
    width: 680px;
    height: 388px;
    background: var(--white);
    border-radius: 16px;
    overflow: hidden;
    box-shadow: 0 6px 22px rgba(0,0,0,0.14);
  }
  .card-front { top: 36px; }
  .card-back { top: 456px; }

  /* Front */
  .front-band {
    position: absolute;
    left: 0; right: 0; bottom: 0;
    height: 96px;
    background: var(--brown);
  }
  .front-photo {
    position: absolute;
    left: 90px; right: 20px; top: 24px;
    height: 292px;
    border-radius: 40% 40% 20% 20% / 50% 50% 12% 12%;
    background:
      radial-gradient(ellipse 22% 38% at 30% 42%, #d98c42 0%, rgba(217,140,66,0) 100%),
      radial-gradient(ellipse 24% 42% at 46% 52%, #c97b3a 0%, rgba(201,123,58,0) 100%),
      radial-gradient(ellipse 26% 44% at 72% 36%, #6d6058 0%, rgba(109,96,88,0) 100%),
      radial-gradient(ellipse 22% 40% at 20% 70%, #4f4038 0%, rgba(79,64,56,0) 100%),
      radial-gradient(ellipse 22% 36% at 62% 70%, #8a7f78 0%, rgba(138,127,120,0) 100%),
      #eee9e4;
  }
  .front-url {
    position: absolute;
    right: 40px; bottom: 30px;
    margin: 0;
    font-family: "Questrial", sans-serif;
    font-size: 17px;
    letter-spacing: 4px;
    color: var(--yellow);
  }

  /* Back */
  .brand {
    position: absolute;
    left: 52px; top: 128px;
    width: 240px;
    display: flex;
    align-items: center;
    gap: 12px;
  }
  .brand-mark {
    width: 26px; height: 26px;
    background: var(--yellow);
    flex: none;
  }
  .brand-name {
    font-family: "Montserrat", sans-serif;
    font-weight: 700;
    font-size: 25px;
    line-height: 1.15;
    color: var(--brown);
  }
  .divider {
    position: absolute;
    left: 310px; top: 70px;
    width: 1px; height: 150px;
    background: var(--line);
  }
  .person {
    position: absolute;
    left: 346px; top: 56px;
  }
  .person-name {
    font-family: "Montserrat", sans-serif;
    font-weight: 600;
    font-size: 24px;
    letter-spacing: -0.5px;
    color: var(--text-dark);
    margin: 0;
  }
  .person-role {
    font-family: "Questrial", sans-serif;
    font-size: 17px;
    color: var(--yellow);
    margin: 2px 0 0;
  }
  .contacts {
    position: absolute;
    left: 346px; top: 140px;
    margin: 0; padding: 0;
    list-style: none;
    font-family: "Questrial", sans-serif;
    font-size: 16px;
    color: var(--text-dark);
  }
  .contacts li {
    display: flex;
    align-items: center;
    gap: 8px;
    height: 26px;
  }
  .contact-icon { width: 18px; height: 18px; flex: none; }
  .wave {
    position: absolute;
    left: 0; top: 0;
    width: 680px; height: 388px;
  }
</style>
</head>
<body>
<main class="canvas">

  <section class="card card-front" aria-label="Card front">
    <div class="front-band"></div>
    <div class="front-photo" role="img" aria-label="Photo of five kittens huddled together, ginger and grey tabby"></div>
    <p class="front-url">www.purrnestnookco.com</p>
  </section>

  <section class="card card-back" aria-label="Card back">
    <svg class="wave" viewBox="0 0 680 388" aria-hidden="true">
      <path d="M0,388 L0,354 C220,358 420,342 545,302 C605,281 645,268 680,262 L680,388 Z" fill="var(--brown)"/>
      <path d="M0,342 C220,346 420,330 540,290 C600,268 640,255 680,248" fill="none" stroke="var(--yellow)" stroke-width="4"/>
    </svg>

    <div class="brand">
      <span class="brand-mark"></span>
      <span class="brand-name">Purrnest Nook Co</span>
    </div>

    <div class="divider"></div>

    <div class="person">
      <h1 class="person-name">EMPLOYEE NAME</h1>
      <p class="person-role">Manager</p>
    </div>

    <ul class="contacts">
      <li>
        <svg class="contact-icon" viewBox="0 0 18 18" aria-hidden="true">
          <circle cx="9" cy="9" r="8" fill="none" stroke="var(--yellow)" stroke-width="1.6"/>
          <path d="M6,5 L7.5,5 L8,7 L7,7.8 C7.5,9 8.5,10 9.8,10.6 L10.5,9.6 L12.5,10.2 L12.5,11.8 C9,12 6,9 6,5 Z" fill="var(--yellow)"/>
        </svg>
        +1 (808) 571 6023
      </li>
      <li>
        <svg class="contact-icon" viewBox="0 0 18 18" aria-hidden="true">
          <circle cx="9" cy="9" r="8" fill="none" stroke="var(--yellow)" stroke-width="1.6"/>
          <rect x="5" y="6" width="8" height="6" fill="var(--yellow)"/>
          <path d="M5,6 L9,9.2 L13,6" fill="none" stroke="var(--white)" stroke-width="1"/>
        </svg>
        support@purrnestnookco.com
      </li>
      <li>
        <svg class="contact-icon" viewBox="0 0 18 18" aria-hidden="true">
          <circle cx="9" cy="9" r="8" fill="none" stroke="var(--yellow)" stroke-width="1.6"/>
          <circle cx="9" cy="9" r="4.5" fill="none" stroke="var(--yellow)" stroke-width="1.2"/>
          <path d="M4.5,9 H13.5 M9,4.5 V13.5" stroke="var(--yellow)" stroke-width="1"/>
        </svg>
        www.purrnestnookco.com
      </li>
    </ul>
  </section>

</main>
</body>
</html>
```